wordpress website Carla Winfield, Author, Speaker and Coach

Need a wordpress blogging website for author/speaker/coach.
I have paid for hosting on nestparrot.
I am currently writing a book - Launchpad to Campus - Steps and strategies to prepare you to thrive in college and beyond. Eventually, I will have an Academic/Life Coaching program targeting high school and college students. This website's purpose is to build my email list. I can offer the following reports as incentive for email sign-up:
1. Six Habits That Get Your Teen Through University On Schedule and Debt-Light
2. Surprising Routes to Fund Your Degree
3. SAT/ACT vocabulary word of the day

facebook page: https://www.facebook.com/Carla-Winfield-AcademicLife-Coach-918273645501928/

I would like to have these pages:

1. Home or About page

High school is becoming more and more stressful for students. Not only are they taking more AP classes than ever before, and often spending $1,000’s on SAT/ACT prep programs, most are NOT prepared for success in college. Only 19% of students are graduating from college within 4 years and only 56% are graduating within 6 years. With the cost of higher education skyrocketing, each extra year of school can costs families $40,000 - $60,000 when you factor in living expenses. Then, when students do graduate, they are often underemployed.

Carla's approach is whole person oriented. Her programs help students learn life skills in addition to the study, time management skills, etc. offered by most academic coaching programs. Our program addresses all of the major causes of failure to graduate within 4 years, and is based on sound educational research. Carla's program initially provides the daily interaction needed to successfully change behaviors and seat new success habits, unlike many programs in which students interact with coaches only once a week.
Bio
Carla Winfield is a certified teacher and holds advanced certification in academic coaching and tutoring. She also is a certified trainer in the Morris Tellwright Achievement Keys. She has three successful adult children, and helped them overcome learning differences and thrive.

2. Blog

3. Contact - Include form (I split time between USA and Saudi Arabia, so I will call or email people back, but don't want to leave a phone number)
info@carlawinfield.example

4. Store – 1 book for now
Launchpad to Campus
Steps and strategies to prepare you to thrive in college and beyond
Available 12/01/2017
I could make a preview chapter available for download

5. Speaking
Carla Winfield is available for keynote addresses and half-day, full day or multi-day workshops. I will develop details later

6.Coaching programs
I will develop details later

Target Market(s)

high school students who are college bound and their parents

Number of Pages Required

5+ page

Font styles to use
Sans Serif

Colors

Designer to choose colors to be used in the design.

Requirements
Nice to have
• integration with post finch for contact management

```html
<!DOCTYPE html>
<html lang="en">
<head>
<meta charset="utf-8">
<title>Carla Winfield — Author, Speaker and Coach</title>
<link rel="stylesheet" href="https://fonts.googleapis.com/css2?family=Cabin:wght@400;500;600;700&family=Open+Sans:ital,wght@0,400;0,600;0,700;1,400&display=swap">
<style>
:root{
  --green:#0f8043;
  --green-dark:#0b6e38;
  --lime:#8dc63f;
  --purple:#9b97d4;
  --ink:#2b2b2b;
  --text:#555;
  --muted:#8a8a8a;
  --line:#d9d9d9;
  --grey-bg:#f3f3f3;
  --footer-bar:#2e2e2e;
  --white:#fff;
  --share-blue:#3b5998;
  --share-red:#dd4b39;
  --share-sky:#1da1f2;
}
*{box-sizing:border-box;margin:0;padding:0}
html,body{width:1200px;height:2965px;overflow:hidden}
body{position:relative;font-family:"Open Sans",Arial,sans-serif;color:var(--text);background:var(--white)}
.abs{position:absolute}
h1,h2,h3,h4{font-family:"Cabin",Arial,sans-serif;font-weight:600}
a{color:inherit;text-decoration:none}

/* header + hero */
.top-rule{left:0;top:0;width:1200px;height:3px;background:var(--purple);z-index:3}
.hero-photo{left:0;top:0;width:1200px;height:656px;background:linear-gradient(100deg,#cfd9de 0%,#e9eef0 25%,#b9a48e 45%,#d8cfc4 60%,#8d9aa4 80%,#c8d3d8 100%)}
.brand{left:99px;top:96px;display:flex;align-items:center;gap:12px;font-family:"Cabin",sans-serif;font-weight:600;font-size:30px;color:var(--green)}
.brand-dot{width:26px;height:26px;border-radius:50%;background:var(--lime)}
.top-mail{right:324px;top:28px;display:flex;align-items:center;gap:8px;font-size:13.5px;color:var(--ink);white-space:nowrap}
.ebook-btn{left:890px;top:22px;width:211px;height:35px;background:var(--purple);color:var(--white);font-size:14px;display:flex;align-items:center;justify-content:center;gap:10px}
.nav{right:99px;top:82px;display:flex;gap:28px;font-size:14px;color:var(--ink)}
.nav .active{color:var(--green);font-weight:600;border-bottom:2px solid var(--purple);padding-bottom:4px}
.hero-band{left:0;top:530px;width:1200px;height:126px;background:rgba(15,128,67,.9)}
.hero-title{left:99px;top:556px;font-size:35px;color:var(--white);font-weight:600;letter-spacing:.5px}
.hero-sub{left:101px;top:607px;font-size:17px;color:var(--white);font-weight:600}
.btn-lime{left:763px;top:573px;width:158px;height:44px;background:var(--lime);color:var(--white);font-family:"Cabin",sans-serif;font-weight:600;font-size:15px;display:flex;align-items:center;justify-content:center}
.btn-outline{left:941px;top:573px;width:160px;height:44px;border:2px solid var(--white);color:var(--white);font-family:"Cabin",sans-serif;font-weight:600;font-size:15px;display:flex;align-items:center;justify-content:center}

/* ornament divider */
.divider{height:14px;display:flex;align-items:center}
.divider::before,.divider::after{content:"";flex:1;height:1px;background:var(--line)}
.divider span{width:8px;height:8px;border-radius:50%;background:var(--purple);margin:0 10px}
.divider.left::before{flex:0 0 0}
.divider.dark::before,.divider.dark::after{background:#777}

/* about */
.about-title{left:99px;top:706px;font-size:33px;color:var(--ink)}
.accent{color:var(--lime)}
.about-text{left:99px;top:800px;width:510px;font-size:13.5px;line-height:22px;color:var(--text);text-align:justify}
.about-text p+p{margin-top:14px}
.btn-green{background:var(--green);color:var(--white);font-size:14px;display:flex;align-items:center;justify-content:center;gap:8px}
.video-frame{left:656px;top:708px;width:445px;height:277px;border-radius:14px;background:#111;padding:26px 30px}
.video-frame .screen{width:100%;height:100%;background:linear-gradient(135deg,#3a2a22,#8a6b57 45%,#2a2a2a);border-radius:4px}
.video-shadow{left:676px;top:988px;width:405px;height:18px;background:radial-gradient(ellipse at center,rgba(0,0,0,.18),transparent 70%)}

/* programs */
.programs-bg{left:0;top:1044px;width:1200px;height:316px;background:linear-gradient(90deg,#141414,#2a2a2a 50%,#161616)}
.programs-lower{left:0;top:1360px;width:1200px;height:478px;background:var(--grey-bg)}
.section-title{width:1200px;text-align:center;font-size:32px}
.programs-title{top:1088px;color:var(--white)}
.programs-sub{top:1173px;width:1200px;text-align:center;font-size:13.5px;color:#ddd}
.program-card{top:1216px;width:484px;height:247px;border:3px solid var(--white);color:var(--white);text-align:center;padding-top:26px}
.program-card.coaching{left:99px;background:var(--green)}
.program-card.speaking{left:617px;background:var(--lime)}
.program-card h3{font-size:27px;font-weight:500;letter-spacing:1px;margin-top:12px}
.program-card p{font-size:13px;line-height:17px;width:420px;margin:6px auto 0}
.card-btn{width:126px;height:33px;margin:14px auto 0;background:var(--white);font-size:13.5px;display:flex;align-items:center;justify-content:center;gap:6px}
.coaching .card-btn{color:var(--green)}
.speaking .card-btn{color:var(--lime)}

/* store */
.book-cover{left:123px;top:1530px;width:180px;height:260px;background:linear-gradient(100deg,#0c0c0c,#2b2b2b 60%,#151515);box-shadow:8px 10px 18px rgba(0,0,0,.25)}
.store-title{left:324px;top:1545px;font-size:32px;color:var(--ink)}
.store-divider{left:324px;top:1596px;width:777px}
.store-headline{left:324px;top:1629px;width:777px;font-family:"Cabin",sans-serif;font-size:16.5px;color:var(--ink);font-weight:500;white-space:nowrap}
.store-text{left:324px;top:1662px;width:777px;font-size:13px;line-height:20px}
.store-date{left:324px;top:1726px;font-size:17px;color:var(--ink);font-weight:700;display:flex;align-items:center;gap:10px}
.preview-btn{left:542px;top:1716px;width:253px;height:38px;background:var(--purple);color:var(--white);font-size:14px;display:flex;align-items:center;justify-content:center;gap:10px}

/* blog */
.blog-title{top:1892px;color:var(--ink)}
.blog-divider{left:470px;top:1950px;width:260px}
.post{top:1999px;width:313px}
.post-img{height:148px}
.post-date{left:0;top:4px;width:50px;height:62px;background:var(--lime);color:var(--white);text-align:center;font-family:"Cabin",sans-serif;line-height:1}
.post-date b{display:block;font-size:22px;margin-top:6px}
.post-date small{display:block;font-size:11px;margin-top:2px}
.post h4{font-size:16px;color:var(--ink);font-weight:600;margin-top:16px}
.post-meta{display:flex;align-items:center;gap:8px;font-size:11.5px;color:var(--text);margin-top:10px}
.post-meta .sep{color:var(--muted)}
.post p{font-size:11px;line-height:17px;color:var(--text);margin-top:12px}

/* newsletter */
.newsletter{left:0;top:2299px;width:1200px;height:326px;background:linear-gradient(90deg,#0d7a3f,#12894a 50%,#0d7a3f)}
.newsletter-title{top:2374px;color:var(--white);font-weight:500;font-size:33px}
.newsletter-sub{top:2438px;width:1200px;text-align:center;font-style:italic;color:#e6f3ea;font-size:14px}
.news-input{left:241px;top:2493px;width:451px;height:45px;background:var(--white);border-radius:3px;font-size:13px;color:#888;display:flex;align-items:center;padding-left:16px}
.news-btn{left:710px;top:2493px;width:219px;height:45px;background:var(--lime);color:var(--white);font-size:14px;display:flex;align-items:center;justify-content:center;letter-spacing:.5px}

/* footer */
.foot-head{top:2672px;font-size:19px;color:var(--ink);font-weight:600;letter-spacing:.5px;padding-bottom:10px;border-bottom:1px solid var(--line)}
.contact-list{left:99px;top:2718px;width:250px;font-size:13px;color:var(--ink)}
.contact-list li{list-style:none;display:flex;gap:16px;align-items:flex-start;margin-bottom:18px;line-height:19px}
.contact-list svg{flex:0 0 18px;margin-top:1px}
.contact-list .mail{font-size:12.5px;white-space:nowrap}
.field{border:1px solid #ddd;font-size:12px;color:#666;padding:8px 10px}
.submit-btn{left:433px;top:2847px;width:97px;height:32px;background:var(--green);color:var(--white);font-size:13px;display:flex;align-items:center;justify-content:center}
.footer-brand{left:930px;top:2766px;display:flex;align-items:center;gap:10px;font-family:"Cabin",sans-serif;font-weight:600;font-size:24px;color:var(--green)}
.share{left:1158px;width:42px;height:42px}
.copyright{left:0;top:2922px;width:1200px;height:43px;background:var(--footer-bar);color:var(--white);font-size:13px;display:flex;align-items:center;justify-content:center}
</style>
</head>
<body>

<header>
  <div class="abs hero-photo" role="img" aria-label="Photo of two students studying together at a desk with a tablet"></div>
  <div class="abs top-rule"></div>
  <a class="abs brand" href="#"><span class="brand-dot"></span>Carla Winfield</a>
  <div class="abs top-mail">
    <svg width="20" height="20" viewBox="0 0 20 20"><path d="M5 3l3 3-2 2c1 2 3 4 5 5l2-2 3 3-2 3C8 17 3 12 2 5z" fill="none" stroke="var(--green)" stroke-width="1.6"/></svg>
    info@carlawinfield.example
  </div>
  <a class="abs ebook-btn" href="#">
    <svg width="18" height="14" viewBox="0 0 18 14"><rect x="1" y="1" width="16" height="12" fill="none" stroke="#fff" stroke-width="1.5"/><path d="M9 1v12" stroke="#fff" stroke-width="1.5"/></svg>
    Download Free EBook
  </a>
  <nav class="abs nav">
    <a class="active" href="#">Home</a><a href="#">About Us</a><a href="#">Speaking</a><a href="#">Coaching Programs</a><a href="#">Store</a><a href="#">Blog</a><a href="#">Contact Us</a>
  </nav>
  <div class="abs hero-band"></div>
  <h1 class="abs hero-title">LEARNING ANY WHERE ANY TIME</h1>
  <p class="abs hero-sub">We Help Students Reach Their Life Goals Faster And More Efficiently.</p>
  <a class="abs btn-lime" href="#">BUY TODAY !</a>
  <a class="abs btn-outline" href="#">CONTACT NOW!</a>
</header>

<section class="about">
  <h2 class="abs about-title">ABOUT <span class="accent">CARLAWINFIELD</span></h2>
  <div class="abs divider left" style="left:99px;top:760px;width:494px"><span></span></div>
  <div class="abs about-text">
    <p>Carla Winfield is a certified teacher and holds advanced certification in academic coaching and tutoring. She also is a certified trainer in the Morris Tellwright Achievement Keys. She has three successful adult children, and helped them overcome learning differences and thrive.</p>
    <p>Lorem Ipsum is simply dummy text of the printing and typesetting industry. Lorem Ipsum has been the industry's standard dummy text ever since.</p>
  </div>
  <a class="abs btn-green" href="#" style="left:99px;top:951px;width:128px;height:34px">Read More <span>»</span></a>
  <div class="abs video-frame"><div class="screen" role="img" aria-label="Introductory video of Carla Winfield"></div></div>
  <div class="abs video-shadow"></div>
</section>

<section class="programs">
  <div class="abs programs-bg" role="img" aria-label="Dark photo of a classroom"></div>
  <div class="abs programs-lower"></div>
  <h2 class="abs section-title programs-title">OUR PROGRAMS</h2>
  <div class="abs divider dark" style="left:500px;top:1140px;width:200px"><span></span></div>
  <p class="abs programs-sub">Lorem Ipsum is simply dummy text of the printing and typesetting industry. Lorem Ipsum has been the industry's</p>

  <article class="abs program-card coaching">
    <svg width="60" height="50" viewBox="0 0 60 50"><circle cx="20" cy="14" r="7" fill="#fff"/><circle cx="40" cy="14" r="7" fill="#fff"/><path d="M6 46c0-10 6-16 14-16s14 6 14 16zM26 46c0-10 6-16 14-16s14 6 14 16z" fill="#fff"/><path d="M36 4l3 3 6-6" stroke="var(--green)" stroke-width="2" fill="none"/></svg>
    <h3>COACHING PROGRAMS</h3>
    <p>Lorem Ipsum is simply dummy text of the printing and typesetting industry. Lorem Ipsum has been the industry's</p>
    <a class="card-btn" href="#">Read More <span>»</span></a>
  </article>
  <article class="abs program-card speaking">
    <svg width="60" height="50" viewBox="0 0 60 50"><circle cx="18" cy="22" r="7" fill="#fff"/><path d="M4 48c0-10 6-15 14-15s14 5 14 15z" fill="#fff"/><rect x="30" y="2" width="26" height="18" rx="2" fill="none" stroke="#fff" stroke-width="2"/><path d="M36 20l-4 6 8-6" fill="#fff"/><path d="M35 9h16M35 14h10" stroke="#fff" stroke-width="2"/></svg>
    <h3>SPEAKING PROGRAMS</h3>
    <p>Lorem Ipsum is simply dummy text of the printing and typesetting industry. Lorem Ipsum has been the industry's</p>
    <a class="card-btn" href="#">Read More <span>»</span></a>
  </article>
</section>

<section class="store">
  <div class="abs book-cover" role="img" aria-label="Cover of the book Launchpad to Campus by Carla Winfield"></div>
  <h2 class="abs store-title">OUR <span class="accent">STORE</span></h2>
  <div class="abs divider left store-divider"><span></span></div>
  <p class="abs store-headline">1 book for now Launchpad to Campus Steps and strategies to prepare you to thrive in college and beyond</p>
  <p class="abs store-text">Lorem Ipsum is simply dummy text of the printing and typesetting industry. Lorem Ipsum has been the industry's standard dummy text ever since the 1500s, when an unknown printer took a galley of type and scrambled it</p>
  <p class="abs store-date">
    <svg width="18" height="18" viewBox="0 0 18 18"><rect x="1" y="3" width="16" height="14" fill="var(--ink)"/><rect x="3" y="7" width="12" height="8" fill="#fff"/><path d="M5 1v4M13 1v4" stroke="var(--ink)" stroke-width="2"/></svg>
    Available 12/01/2017
  </p>
  <a class="abs preview-btn" href="#">
    <svg width="18" height="14" viewBox="0 0 18 14"><rect x="1" y="1" width="16" height="12" fill="none" stroke="#fff" stroke-width="1.5"/><path d="M9 1v12" stroke="#fff" stroke-width="1.5"/></svg>
    Download Preview Chapter
  </a>
</section>

<section class="blog">
  <h2 class="abs section-title blog-title">LATEST <span class="accent">BLOG</span></h2>
  <div class="abs divider blog-divider"><span></span></div>

  <article class="abs post" style="left:99px">
    <div class="post-img" role="img" aria-label="Photo of a presenter in front of a projection screen" style="background:linear-gradient(120deg,#6d6258,#c9c2b4 50%,#4f4a44)"></div>
    <div class="abs post-date"><b>07</b><small>Apr<br>2015</small></div>
    <h4>Duis Autem Vel Eum Iriure Dolor In</h4>
    <div class="post-meta"><svg width="11" height="11" viewBox="0 0 11 11"><circle cx="5.5" cy="3" r="2.5" fill="var(--purple)"/><path d="M1 11c0-4 2-5 4.5-5S10 7 10 11z" fill="var(--purple)"/></svg>Dara Quell <span class="sep">/</span><svg width="12" height="12" viewBox="0 0 12 12"><rect x="1" y="2" width="9" height="9" fill="none" stroke="var(--purple)"/><path d="M5 7l6-6" stroke="var(--purple)"/></svg>3 Comments</div>
    <p>Shoe street style leather tote oversized sweatshirt B.R.T. Velmora pebbled crop slipper denim shorts...[+]</p>
  </article>
  <article class="abs post" style="left:443px">
    <div class="post-img" role="img" aria-label="Photo of a teacher standing in front of students" style="background:linear-gradient(120deg,#e8e8e8,#9a8f86 50%,#f1f1f1)"></div>
    <div class="abs post-date"><b>07</b><small>Apr<br>2015</small></div>
    <h4>Duis Autem Vel Eum Iriure Dolor In</h4>
    <div class="post-meta"><svg width="11" height="11" viewBox="0 0 11 11"><circle cx="5.5" cy="3" r="2.5" fill="var(--purple)"/><path d="M1 11c0-4 2-5 4.5-5S10 7 10 11z" fill="var(--purple)"/></svg>Dara Quell <span class="sep">/</span><svg width="12" height="12" viewBox="0 0 12 12"><rect x="1" y="2" width="9" height="9" fill="none" stroke="var(--purple)"/><path d="M5 7l6-6" stroke="var(--purple)"/></svg>3 Comments</div>
    <p>Shoe street style leather tote oversized sweatshirt B.R.T. Velmora pebbled crop slipper denim shorts...[+]</p>
  </article>
  <article class="abs post" style="left:785px">
    <div class="post-img" role="img" aria-label="Photo of a cheerful group of students" style="background:linear-gradient(120deg,#c8a890,#e0c6b0 45%,#8e9fb8)"></div>
    <div class="abs post-date"><b>07</b><small>Apr<br>2015</small></div>
    <h4>Duis Autem Vel Eum Iriure Dolor In</h4>
    <div class="post-meta"><svg width="11" height="11" viewBox="0 0 11 11"><circle cx="5.5" cy="3" r="2.5" fill="var(--purple)"/><path d="M1 11c0-4 2-5 4.5-5S10 7 10 11z" fill="var(--purple)"/></svg>Dara Quell <span class="sep">/</span><svg width="12" height="12" viewBox="0 0 12 12"><rect x="1" y="2" width="9" height="9" fill="none" stroke="var(--purple)"/><path d="M5 7l6-6" stroke="var(--purple)"/></svg>3 Comments</div>
    <p>Shoe street style leather tote oversized sweatshirt B.R.T. Velmora pebbled crop slipper denim shorts...[+]</p>
  </article>
</section>

<section class="newsletter-section">
  <div class="abs newsletter"></div>
  <h2 class="abs section-title newsletter-title">Subscribe To Our Newsletter</h2>
  <p class="abs newsletter-sub">Sign Up To Receive Email Updates About Courses</p>
  <div class="abs news-input">Enter your email</div>
  <a class="abs news-btn" href="#">SUBSCRIBE</a>
</section>

<footer>
  <h3 class="abs foot-head" style="left:99px;width:240px">CONTACT <span class="accent">DETAILS</span></h3>
  <ul class="abs contact-list">
    <li><svg width="18" height="22" viewBox="0 0 18 22"><path d="M9 1a7 7 0 0 1 7 7c0 5-7 13-7 13S2 13 2 8a7 7 0 0 1 7-7z" fill="none" stroke="var(--lime)" stroke-width="1.6"/><circle cx="9" cy="8" r="2.5" fill="var(--lime)"/></svg>Lorem Ipsum is simply dummy text of the printing -0000000</li>
    <li><svg width="18" height="14" viewBox="0 0 18 14"><rect x="1" y="1" width="16" height="12" fill="var(--lime)"/><path d="M1 1l8 7 8-7" fill="none" stroke="#fff" stroke-width="1.4"/></svg><span class="mail">appointment@carlawinfield.example</span></li>
    <li><svg width="18" height="18" viewBox="0 0 20 20"><path d="M5 2l3 4-2 2c1 2 3 4 5 5l2-2 4 3-2 3C8 17 3 12 2 5z" fill="var(--lime)"/></svg><span style="font-size:17px">123 456 7890</span></li>
  </ul>

  <h3 class="abs foot-head" style="left:433px;width:403px">QUICK <span class="accent">INQUIRY</span></h3>
  <div class="abs field" style="left:433px;top:2718px;width:196px;height:30px">Name</div>
  <div class="abs field" style="left:641px;top:2718px;width:195px;height:30px">Email Id</div>
  <div class="abs field" style="left:433px;top:2760px;width:403px;height:77px">Query</div>
  <a class="abs submit-btn" href="#">Submit</a>

  <div class="abs footer-brand"><span class="brand-dot"></span>Carla Winfield</div>

  <a class="abs share" href="#" aria-label="Share link one" style="top:2708px;background:var(--share-blue)"></a>
  <a class="abs share" href="#" aria-label="Share link two" style="top:2754px;background:var(--share-red)"></a>
  <a class="abs share" href="#" aria-label="Share link three" style="top:2800px;background:var(--share-sky)"></a>

  <div class="abs copyright">© 2017 Carla Winfield .All Rights Reserved</div>
</footer>

</body>
</html>
```